Corvin Ridge Software PowerPoint template

We are a software company selling endpoint visibility, access and security technology to enterprise-level IT departments.
Our technology helps organizations gain comprehensive visibility into and control over devices accessing their corporate network so they can quickly identify and address suspicious activity on the network that could lead to potential threats like data breaches.
This technology can cost organizations upwards of $1M - depending on the size of the organization. Our primary clients are Vestral 2,000 companies.
We want a professional, polished PowerPoint template that we can use for all company presentations. Please include:
Title page
Section page
General info page
Thank you page
Logo options and color specs are attached.
Please include our tagline on at least the title page: Discover the edge. Optimize the whole.
Reason: Seeking more options. Looking for a clean design that uses lots of white space.
Software

```html
<!DOCTYPE html>
<html lang="en">
<head>
<meta charset="UTF-8">
<title>Corvin Ridge Software – Title Presentation</title>
<link href="https://fonts.googleapis.com/css2?family=PT+Sans+Narrow:wght@400;700&family=Fira+Sans+Condensed:wght@500;600&display=swap" rel="stylesheet">
<style>
  :root {
    --brand-red: #8c1c22;
    --accent-copper: #c67a4e;
    --bar-grey: #b3b3b3;
    --body-grey: #6b6b6b;
    --rule-red: #b5463f;
    --dot-grey: #e4e4e4;
    --paper: #ffffff;
  }
  * { box-sizing: border-box; margin: 0; padding: 0; }
  html, body {
    width: 1200px; height: 675px; overflow: hidden; background: var(--paper);
  }
  .slide {
    position: relative; width: 1200px; height: 675px; background: var(--paper);
    font-family: "Fira Sans Condensed", "PT Sans Narrow", sans-serif;
  }
  .top-bar { position: absolute; top: 0; left: 0; height: 16px; width: 960px; background: var(--bar-grey); }
  .top-bar-accent { position: absolute; top: 0; left: 960px; height: 16px; width: 240px; background: var(--brand-red); }
  .corner-texture {
    position: absolute; top: 16px; left: 0; width: 90px; height: 165px;
    background: radial-gradient(ellipse at 20% 30%, var(--dot-grey) 0%, rgba(255,255,255,0) 75%);
  }
  .slide-title {
    position: absolute; left: 84px; top: 46px;
    font-family: "PT Sans Narrow", sans-serif; font-weight: 700;
    font-size: 64px; line-height: 1; color: var(--brand-red); letter-spacing: -0.5px;
  }
  .slide-subtitle {
    position: absolute; left: 96px; top: 114px;
    font-family: "Fira Sans Condensed", sans-serif; font-weight: 600;
    font-size: 27px; line-height: 1; color: var(--accent-copper);
  }
  .content-column {
    position: absolute; width: 470px;
    font-weight: 500; font-size: 18px; line-height: 22.5px; color: var(--body-grey);
  }
  .content-column p + p { margin-top: 22px; }
  .content-column p.spaced { margin-top: 30px; }
  .column-left { left: 101px; top: 210px; }
  .column-right { left: 634px; top: 205px; }
  .footer-rule { position: absolute; left: 71px; top: 626px; width: 1099px; height: 1.5px; background: var(--rule-red); }
  .footer-brand {
    position: absolute; right: 30px; top: 637px;
    display: flex; align-items: center; gap: 7px;
    font-family: "Fira Sans Condensed", sans-serif; font-weight: 600;
    font-size: 14px; letter-spacing: 1px; color: var(--brand-red); text-transform: uppercase;
  }
  .footer-brand .brand-dot { width: 12px; height: 12px; border-radius: 50%; background: var(--brand-red); }
</style>
</head>
<body>
  <div class="slide">
    <div class="top-bar"></div>
    <div class="top-bar-accent"></div>
    <div class="corner-texture" role="img" aria-label="Faint decorative dot texture in the top-left corner"></div>

    <h1 class="slide-title">TITLE PRESENTATION</h1>
    <h2 class="slide-subtitle">Subtitle Presentation</h2>

    <div class="content-column column-left">
      <p>Lorem ipsum dolor sit amet, consectetuer adipiscing elit. Maecenas porttitor congue massa.</p>
      <p>Lorem ipsum dolor sit amet, consectetuer adipiscing elit. Maecenas porttitor congue massa. Fusce posuere, magna sed pulvinar ultricies, purus lectus malesuada libero, sit amet commodo magna eros quis urna.</p>
      <p class="spaced">Lorem ipsum dolor sit amet, consectetuer adipiscing elit. Maecenas porttitor congue massa.</p>
      <p>Lorem ipsum dolor sit amet, consectetuer adipiscing elit. Maecenas porttitor congue massa. Fusce posuere, magna sed pulvinar ultricies, purus lectus malesuada libero, sit amet commodo magna eros quis urna.</p>
    </div>

    <div class="content-column column-right">
      <p>Lorem ipsum dolor sit amet, consectetuer adipiscing elit. Maecenas porttitor congue massa.</p>
      <p>Lorem ipsum dolor sit amet, consectetuer adipiscing elit. Maecenas porttitor congue massa. Fusce posuere, magna sed pulvinar ultricies, purus lectus malesuada libero, sit amet commodo magna eros quis urna.</p>
      <p class="spaced">Lorem ipsum dolor sit amet, consectetuer adipiscing elit. Maecenas porttitor congue massa.</p>
      <p>Lorem ipsum dolor sit amet, consectetuer adipiscing elit. Maecenas porttitor congue massa. Fusce posuere, magna sed pulvinar ultricies, purus lectus malesuada libero, sit amet commodo magna eros quis urna.</p>
    </div>

    <div class="footer-rule"></div>
    <div class="footer-brand">
      <span class="brand-dot"></span>
      <span class="brand-name">Corvin Ridge Software</span>
    </div>
  </div>
</body>
</html>
```